Pinecroft Ridge A4 Potrait foldout brochure

We need a brochure design for this residential land development. I have attached the a style that we like to base our design on. Full colour required. will provide files required for design also. PLEASE DO NOT COPY THIS DESIGN. Come up with a new style that gives you this feeling. Please note the plan needs to be positioned landscape on the inside 2 A4 Pages.

Industry/Entity Type

Residential

Font styles to use
Other font styles liked:
• Try with Century Gothich

Requirements
Must have
• use same colours as supplied in Pinecroft ridge brochure.
Nice to have
• nice modern simple background graphics

```html
<!DOCTYPE html>
<html lang="en">
<head>
<meta charset="utf-8">
<title>Pinecroft Ridge – Brochure Cover</title>
<link rel="stylesheet" href="https://fonts.googleapis.com/css2?family=Questrial&family=Lato:wght@400;700&display=swap">
<style>
  :root {
    --green-deep: #064a1f;
    --green-main: #0b5a2a;
    --green-card: #054a1d;
    --green-text: #0d4d25;
    --white: #ffffff;
    --orange: #f7a04a;
    --purple: #a77cc4;
    --pink: #dba3c8;
    --meadow: #5bb36a;
    --lime: #8cc863;
    --heading-font: "Questrial", sans-serif;
    --body-font: "Lato", sans-serif;
  }
  * { margin: 0; padding: 0; box-sizing: border-box; }
  html, body { width: 1200px; height: 867px; overflow: hidden; background: #e6e6e6; }
  .brochure { position: relative; width: 1200px; height: 867px; }
  .brochure__backdrop { position: absolute; inset: 0; }
  .fold-line { position: absolute; left: 600px; top: 0; width: 1px; height: 867px; background: rgba(0,0,0,0.08); }

  .contact-card {
    position: absolute; left: 132px; top: 223px; width: 323px; height: 388px;
    background: var(--green-card); border: 1px solid var(--white);
    box-shadow: 0 2px 6px rgba(0,0,0,0.35);
    color: var(--white); text-align: center;
  }
  .contact-card__mark {
    width: 70px; height: 70px; border-radius: 50%; background: var(--lime);
    margin: 34px auto 0;
  }
  .contact-card__name {
    font-family: var(--heading-font); font-size: 36px; font-weight: 400;
    margin-top: 38px; letter-spacing: -0.3px;
  }
  .contact-card__details { margin-top: 22px; font-family: var(--body-font); font-size: 15px; line-height: 20px; }
  .contact-card__address { display: block; }
  .contact-card__phone { display: block; font-weight: 700; font-size: 19px; margin: 8px 0 6px; }
  .contact-card__line { display: block; margin-bottom: 4px; }
  .icon { display: inline-block; vertical-align: -2px; margin-right: 5px; }

  .cover-title {
    position: absolute; right: 70px; top: 250px; text-align: right; color: var(--white);
  }
  .cover-title__name { font-family: var(--heading-font); font-size: 52px; font-weight: 400; letter-spacing: -0.5px; line-height: 1; }
  .cover-title__place { font-family: var(--heading-font); font-size: 11px; margin-top: 2px; }

  .cover-web {
    position: absolute; left: 745px; top: 793px;
    font-family: var(--body-font); font-weight: 700; font-size: 22px; color: var(--green-text);
  }
</style>
</head>
<body>
<main class="brochure">
  <svg class="brochure__backdrop" width="1200" height="867" viewBox="0 0 1200 867">
    <defs>
      <linearGradient id="meadow-tones" x1="0" y1="0" x2="1" y2="0.15">
        <stop offset="0" stop-color="#f59a45"/>
        <stop offset="0.14" stop-color="#f7b454"/>
        <stop offset="0.28" stop-color="#d9a0c6"/>
        <stop offset="0.38" stop-color="#9a7ab8"/>
        <stop offset="0.5" stop-color="#5aae6a"/>
        <stop offset="0.62" stop-color="#b48ad0"/>
        <stop offset="0.74" stop-color="#e3a9c7"/>
        <stop offset="0.86" stop-color="#f4a24c"/>
        <stop offset="1" stop-color="#8cc863"/>
      </linearGradient>
      <linearGradient id="canopy" x1="0" y1="0" x2="0" y2="1">
        <stop offset="0" stop-color="#0b5a2a"/>
        <stop offset="1" stop-color="#0f4f22"/>
      </linearGradient>
    </defs>
    <rect class="meadow-field" width="1200" height="867" fill="url(#meadow-tones)"
          role="img" aria-label="Soft meadow-coloured lattice pattern in orange, pink, purple and green"/>
    <polygon class="canopy" points="0,0 1200,0 1200,375 600,499 0,380" fill="url(#canopy)"/>
    <polyline class="canopy-edge" points="0,372 600,492 1200,367" fill="none" stroke="#ffffff" stroke-width="3"/>
    <polyline class="canopy-edge" points="0,384 600,503 1200,379" fill="none" stroke="#ffffff" stroke-width="2"/>
    <polyline class="canopy-edge" points="0,389 600,508 1200,384" fill="none" stroke="#0b5a2a" stroke-width="3"/>
  </svg>
  <div class="fold-line"></div>

  <section class="contact-card">
    <div class="contact-card__mark"></div>
    <h2 class="contact-card__name">Pinecroft Ridge</h2>
    <div class="contact-card__details">
      <span class="contact-card__address">
        <svg class="icon" width="11" height="14" viewBox="0 0 11 14"><path d="M5.5 0A5.5 5.5 0 0 0 0 5.5C0 9.6 5.5 14 5.5 14S11 9.6 11 5.5A5.5 5.5 0 0 0 5.5 0Zm0 7.6a2.1 2.1 0 1 1 0-4.2 2.1 2.1 0 0 1 0 4.2Z" fill="#fff"/></svg>Pinecroft Ridge<br>
        Larchmont Avenue 58b<br>
        20417 City, State
      </span>
      <span class="contact-card__phone">
        <svg class="icon" width="17" height="17" viewBox="0 0 17 17"><circle cx="8.5" cy="8.5" r="7.5" fill="none" stroke="#fff" stroke-width="1.4"/><path d="M6 4.5l1.4 1.8-.8 1c.6 1.3 1.5 2.2 2.8 2.8l1-.8 1.8 1.4-.9 1.4c-2.9-.4-5.4-2.9-5.8-5.8Z" fill="#fff"/></svg>+01 98 7654321
      </span>
      <span class="contact-card__line">
        <svg class="icon" width="15" height="11" viewBox="0 0 15 11"><rect x="0.6" y="0.6" width="13.8" height="9.8" fill="none" stroke="#fff" stroke-width="1.2"/><path d="M0.6 0.6 7.5 6l6.9-5.4" fill="none" stroke="#fff" stroke-width="1.2"/></svg>info@pinecroftridge.com
      </span>
      <span class="contact-card__line">
        <svg class="icon" width="15" height="15" viewBox="0 0 15 15"><circle cx="7.5" cy="7.5" r="6.6" fill="none" stroke="#fff" stroke-width="1.2"/><ellipse cx="7.5" cy="7.5" rx="3" ry="6.6" fill="none" stroke="#fff" stroke-width="1"/><path d="M1 7.5h13M2 4.2h11M2 10.8h11" stroke="#fff" stroke-width="1"/></svg>www.pinecroftridge.com
      </span>
    </div>
  </section>

  <header class="cover-title">
    <h1 class="cover-title__name">Pinecroft Ridge</h1>
    <p class="cover-title__place">Ashwood Park</p>
  </header>

  <p class="cover-web">www.pinecroftridge.com</p>
</main>
</body>
</html>
```